Website redesign for job agency recruitment

Please refer to the attached document, “Tarvenly Work Website Brief,” for comprehensive details regarding the scope, objectives, and requirements of this website redesign project.

For imagery you can use images from this website https://www.pixelmarrowfoto.com or any other you regularly use.

Target Market(s)

Jobseekers and Companies looking for general labour

Industry/Entity Type

Services: Oil, Gas and Mining, Administrative, Construction and Trades, Warehouse and Logistics and, Manufacturing.

Number of Pages Required

5+ page

Font styles to use
Serif
Other font styles liked:
• Inter, Open-Sans or similar.

Requirements
Must have
• The requirements highlighted in the Word document attached. The final design needs to be provided in Figma including all viewports (Desktop, mobiel and tablet)
Should not have
• Website we like as a reference: www.brevicktalentco.com, www.qelvaworks.com, www.zunmarra.com, www.ferrowhires.com, www.9vtalentpool.com, www.hiringwithtrello.ca

```html
<!DOCTYPE html>
<html lang="en">
<head>
<meta charset="utf-8">
<title>Tarvenly Work Agency</title>
<link href="https://fonts.googleapis.com/css2?family=Archivo:wght@600;700;800&family=Inter:wght@400;500;600;700&display=swap" rel="stylesheet">
<style>
:root{
  --navy:#0d2a78;
  --navy-deep:#0a2366;
  --blue:#1548ad;
  --yellow:#f5c21b;
  --ink:#1b2a5e;
  --body:#4a4f5c;
  --muted:#8a8f9c;
  --pale:#f3f6fc;
  --white:#ffffff;
}
*{box-sizing:border-box;margin:0;padding:0}
html,body{width:1200px;height:4955px;overflow:hidden}
body{font-family:"Inter",sans-serif;color:var(--body);background:var(--white);position:relative}
.abs{position:absolute}
h1,h2,h3,.display{font-family:"Archivo",sans-serif}
.btn{position:absolute;display:flex;align-items:center;justify-content:center;background:var(--yellow);color:var(--ink);font-family:"Inter",sans-serif;font-weight:600;font-size:12px;letter-spacing:.3px;border-radius:30px;text-transform:uppercase}
.accent{color:var(--yellow)}
.rule{position:absolute;height:2px;width:42px;background:var(--ink)}
.rule.light{background:var(--white)}
.section-title{position:absolute;left:0;width:1200px;text-align:center;font-family:"Archivo",sans-serif;font-weight:800;font-size:32px;color:var(--ink);letter-spacing:.3px}

/* header */
.site-header{position:absolute;left:0;top:0;width:1200px;height:133px;background:var(--white)}
.brand{left:150px;top:22px;display:flex;align-items:center;gap:10px}
.brand-mark{width:44px;height:44px;border-radius:50%;background:var(--navy)}
.brand-name{font-family:"Inter",sans-serif;font-weight:700;font-size:20px;color:var(--navy);line-height:1.1}
.brand-sub{font-size:9px;color:var(--navy);font-weight:600;margin-top:2px}
.toll{left:582px;top:30px;font-size:12px;color:var(--ink);font-weight:600;display:flex;align-items:center;gap:8px}
.toll b{color:var(--yellow);font-size:18px;font-weight:700}
.pill-outline{position:absolute;border:2px solid var(--navy);border-radius:20px;color:var(--navy);font-size:12px;font-weight:600;display:flex;align-items:center;justify-content:center}
.main-nav{left:497px;top:78px;display:flex;gap:0;font-size:12.5px;font-weight:500;color:var(--ink);text-transform:uppercase}
.main-nav span{padding:8px 11px;border-radius:20px}
.main-nav .current{background:var(--yellow)}

/* hero */
.hero{left:0;top:133px;width:1200px;height:602px;background:linear-gradient(180deg,#3d6a9a 0%,#8aa9c4 30%,#d9a070 52%,#7b5a48 70%,#3b3236 100%)}
.hero h1{position:absolute;left:148px;top:48px;color:var(--white);font-weight:800;font-size:34px;line-height:44px;letter-spacing:.3px}
.hero-dots{left:555px;top:548px;display:flex;gap:11px}
.hero-dots i{width:13px;height:13px;border-radius:50%;background:var(--white);display:block}
.hero-dots i:first-child{background:var(--yellow)}

/* services */
.services{left:0;top:735px;width:1200px;height:853px;background:var(--white)}
.services-band{left:0;top:0;width:1200px;height:165px;background:linear-gradient(180deg,#f5f7fc,#ffffff)}
.svc-label{position:absolute;width:140px;text-align:center;font-size:12px;color:var(--ink);line-height:18px}
.svc-label.active{color:#d9a514}
.svc-copy h3{font-size:21px;color:var(--ink);font-weight:700;margin-bottom:16px}
.svc-copy p{font-size:11.5px;line-height:17px;color:var(--body)}
.svc-copy .tag{margin-top:20px;font-weight:700;color:var(--ink);font-size:12.5px;line-height:19px}
.photo{position:absolute;border-radius:10px}

/* about */
.about{left:0;top:1588px;width:1200px;height:677px;background:var(--navy)}
.chip{position:absolute;background:#1e3f95;color:var(--white);border-radius:16px;font-size:16px;display:flex;align-items:center;justify-content:center}
.about h2{position:absolute;left:638px;top:125px;color:var(--white);font-size:33px;font-weight:800;line-height:42px}
.about p{position:absolute;left:638px;width:412px;color:#e6ebf7;font-size:12px;line-height:17.5px}
.stats{left:152px;top:2185px;width:898px;height:138px;background:var(--blue);border-radius:8px;display:flex;padding:0 28px;align-items:center;justify-content:space-between}
.stat{display:flex;align-items:center;gap:18px;width:270px}
.stat-icon{width:66px;height:66px;border:2px solid var(--white);border-radius:50%;flex:none}
.stat b{font-family:"Archivo",sans-serif;display:block;color:var(--yellow);font-size:28px;font-weight:800}
.stat span{display:block;color:#e3e9f7;font-size:11px;line-height:16px}

/* recruiting */
.recruit{left:0;top:2265px;width:1200px;height:670px;background:linear-gradient(90deg,#f0f3fa 0%,#ffffff 12%,#ffffff 88%,#f0f3fa 100%)}
.recruit h2{position:absolute;left:153px;top:128px;font-size:32px;font-weight:800;line-height:42px;color:var(--ink)}
.recruit p{position:absolute;left:153px;width:433px;font-size:12.5px;line-height:18.5px;color:var(--muted);text-align:justify}

/* testimonials */
.testimonials{left:0;top:2935px;width:1200px;height:575px;background:var(--pale)}
.t-card{position:absolute;background:var(--white);border-radius:6px;box-shadow:0 6px 24px rgba(20,40,100,.08);text-align:center}
.t-card .q{font-family:"Archivo",sans-serif;color:var(--yellow);font-weight:800;line-height:1}
.t-card p{color:var(--muted)}
.t-side p{font-size:9px;line-height:13px;padding:0 22px}
.t-main p{font-size:12.5px;line-height:19.5px;padding:0 40px}
.author{position:absolute;display:flex;align-items:center;gap:10px}
.avatar{border-radius:50%;background:linear-gradient(135deg,#c7ccd6,#8d96a8);flex:none}
.author b{display:block;color:var(--ink);font-weight:500}
.author span{display:block;color:var(--muted)}
.arrow-btn{position:absolute;width:36px;height:36px;border:1.5px solid #a9b0c0;border-radius:50%}

/* blog */
.blog{left:0;top:3510px;width:1200px;height:670px;background:var(--white)}
.post{position:absolute;top:183px;width:283px;height:435px;background:var(--white);border-radius:4px;box-shadow:0 6px 22px rgba(20,40,100,.09);overflow:hidden}
.post.featured{background:var(--navy)}
.post .img{height:197px}
.post h3{margin:30px 26px 0;font-family:"Inter",sans-serif;font-size:15px;font-weight:700;line-height:21px;color:var(--ink)}
.post.featured h3{color:var(--white)}
.post p{margin:16px 26px 0;font-size:11.5px;line-height:16px;color:var(--muted)}
.post.featured p{color:#d3dbf0}
.post .btn{left:30px;top:372px;width:112px;height:34px}

/* cta */
.cta{left:0;top:4180px;width:1200px;height:375px;background:var(--blue)}
.cta h2{position:absolute;left:0;width:1200px;top:127px;text-align:center;color:var(--white);font-size:44px;font-weight:800;letter-spacing:.5px}
.cta p{position:absolute;left:0;width:1200px;top:200px;text-align:center;color:#e6ecf8;font-size:16px;line-height:27px}

/* footer */
.site-footer{left:0;top:4555px;width:1200px;height:400px;background:var(--navy)}
.foot-brand{left:150px;top:70px;width:222px;height:150px;display:flex;align-items:center;gap:12px}
.foot-brand .brand-mark{width:56px;height:56px;background:var(--white)}
.foot-brand .name{font-weight:700;color:var(--white);font-size:26px;line-height:1.1}
.foot-col h4{color:var(--white);font-size:14px;font-weight:700;text-transform:uppercase}
.foot-col .bar{width:36px;height:2px;background:var(--white);margin:10px 0 22px}
.foot-col li{list-style:none;color:#e7ecf8;font-size:13px;line-height:23px}
.contact-row{display:flex;gap:16px;color:#e7ecf8;font-size:13px;line-height:18px;margin-bottom:20px}
.socials{display:flex;gap:8px}
.socials i{display:block;width:30px;height:30px;border:2px solid var(--white);border-radius:50%}
.copyright{left:0;top:348px;width:1200px;text-align:center;color:#cdd6ee;font-size:12px}
</style>
</head>
<body>

<!-- header -->
<header class="site-header abs">
  <div class="brand abs">
    <span class="brand-mark"></span>
    <div><div class="brand-name">Tarvenly Work</div><div class="brand-sub">Tarvenly Work Agency Ltd.</div></div>
  </div>
  <div class="toll abs">
    <svg width="16" height="16" viewBox="0 0 24 24"><path d="M6.6 10.8a15.1 15.1 0 006.6 6.6l2.2-2.2a1 1 0 011-.25 11.4 11.4 0 003.6.57 1 1 0 011 1V20a1 1 0 01-1 1A17 17 0 013 4a1 1 0 011-1h3.5a1 1 0 011 1c0 1.25.2 2.45.57 3.57a1 1 0 01-.25 1z" fill="#1b2a5e"/></svg>
    TOLL FREE: <b>1-888-555-0142</b>
  </div>
  <div class="pill-outline" style="left:855px;top:24px;width:80px;height:36px">LOGIN</div>
  <div class="btn" style="left:947px;top:24px;width:104px;height:36px;font-weight:500">REGISTER</div>
  <nav class="main-nav abs">
    <span class="current">Home</span><span>Candidates</span><span>Employers</span><span>Services</span><span>About Us</span><span>Contact Us</span>
  </nav>
</header>

<!-- hero -->
<section class="hero abs" role="img" aria-label="Aerial photo of a city skyline at sunset">
  <h1>TARVENLY WORK AGENCY<br>OFFER <span class="accent">VARIOUS OPPORTUNITIES</span><br>IN THE DIFFERENT INDUSTRIES.</h1>
  <div class="btn" style="left:148px;top:202px;width:174px;height:44px">For Candidates</div>
  <div class="btn" style="left:337px;top:202px;width:174px;height:44px">For Employers</div>
  <div class="hero-dots abs"><i></i><i></i><i></i><i></i></div>
</section>

<!-- services -->
<section class="services abs">
  <div class="services-band abs"></div>
  <h2 class="section-title" style="top:52px">OUR <span class="accent">SERVICES</span></h2>
  <div class="rule" style="left:579px;top:115px"></div>

  <svg class="abs" style="left:0;top:0" width="1200" height="480" viewBox="0 0 1200 480">
    <path d="M160 390 C 300 330, 420 315, 598 275 S 900 300, 1045 390" fill="none" stroke="#f5c21b" stroke-width="2"/>
    <circle cx="160" cy="390" r="6" fill="#fff" stroke="#f5c21b" stroke-width="2"/>
    <circle cx="1045" cy="390" r="6" fill="#fff" stroke="#f5c21b" stroke-width="2"/>
    <line x1="262" y1="385" x2="262" y2="432" stroke="#f5c21b" stroke-width="2"/>
    <path d="M257 426 L262 434 L267 426" fill="none" stroke="#f5c21b" stroke-width="2"/>
    <circle cx="262" cy="347" r="38" fill="#f5c21b"/>
    <circle cx="418" cy="300" r="37" fill="#0d2a78"/>
    <circle cx="598" cy="275" r="37" fill="#0d2a78"/>
    <circle cx="772" cy="295" r="37" fill="#0d2a78"/>
    <circle cx="930" cy="335" r="37" fill="#0d2a78"/>
    <g fill="none" stroke="#fff" stroke-width="2">
      <circle cx="418" cy="300" r="10"/><circle cx="418" cy="300" r="4"/>
      <rect x="584" y="262" width="28" height="22" rx="3"/><line x1="584" y1="290" x2="612" y2="290"/>
      <path d="M758 310 V288 L772 280 L786 288 V310 Z"/><rect x="766" y="296" width="12" height="14"/>
      <circle cx="922" cy="330" r="8"/><rect x="914" y="342" width="28" height="8" rx="2"/>
    </g>
    <g fill="none" stroke="#1b2a5e" stroke-width="2">
      <path d="M250 362 L262 330 L274 362 Z"/><line x1="244" y1="362" x2="280" y2="362"/>
    </g>
  </svg>
  <div class="svc-label active" style="left:192px;top:258px">Oil, Gas<br>and Mining</div>
  <div class="svc-label" style="left:348px;top:228px">Administrative</div>
  <div class="svc-label" style="left:528px;top:186px">Construction<br>and Trades</div>
  <div class="svc-label" style="left:705px;top:202px">Warehouse<br>and Logistics</div>
  <div class="svc-label" style="left:867px;top:264px">Manufacturing</div>

  <div class="svc-copy abs" style="left:172px;top:484px;width:285px">
    <h3>Oil, Gas and Mining</h3>
    <p>Tarvenly Work Agency is a premiere Oil, Gas &amp; Mining staffing agency that can provide you with a reliable and experienced workforce. From rig hands to engineers, we provide solutions from temp, temp-to-hire, and permanent positions.</p>
    <p class="tag">We are Oil, Gas &amp; Mining Staffing Advisors –Digging Deeper!</p>
  </div>
  <div class="btn" style="left:172px;top:692px;width:114px;height:34px">Read More</div>

  <div class="abs" style="left:622px;top:438px;width:340px;height:340px;border-radius:50%;background:#fdf4dc"></div>
  <div class="photo" role="img" aria-label="Offshore oil platform on the sea at dusk" style="left:512px;top:417px;width:320px;height:268px;background:linear-gradient(180deg,#1d4f9a 0%,#3e7bc3 55%,#0e2d66 100%)"></div>
  <div class="photo" role="img" aria-label="Excavator working in a gravel quarry" style="left:720px;top:505px;width:330px;height:255px;background:linear-gradient(135deg,#b8bcc2,#7d8087 60%,#c9a23a 100%)"></div>
</section>

<!-- about -->
<section class="about abs">
  <div class="photo" role="img" aria-label="Two colleagues shaking hands across an office table" style="left:150px;top:67px;width:433px;height:465px;background:linear-gradient(135deg,#dfe6ee,#b6c4d3 55%,#e8e1d8 100%)"></div>
  <div class="chip" style="left:640px;top:70px;width:112px;height:34px">About Us</div>
  <h2>TARVENLY WORK AGENCY.<br>THE RIGHT PEOPLE TO<br><span class="accent">POWER YOUR BUSINESS!</span></h2>
  <div class="rule light" style="left:640px;top:272px"></div>
  <p style="top:302px">Tarvenly Work Agency offers a complete range of staffing services to keep pace with your career or operational demands. We understand it's not only daunting but very costly in both time and money to make your business thrive in a rapidly changing environment.</p>
  <p style="top:388px;text-align:justify">Our staffing and recruitment services are not just limited to finding good people. We are a Canada-wide team of capable search specialists, career counselors, HR specialists, and business consultants who enjoy providing our clients with a very customized staffing solution that evolves within their market.</p>
  <div class="btn" style="left:638px;top:502px;width:114px;height:34px">Read More</div>
</section>
<div class="stats abs">
  <div class="stat"><span class="stat-icon"></span><div><b>81%</b><span>Sed ut perspiciatis unde omnis iste natus error sit voluptatem.</span></div></div>
  <div class="stat"><span class="stat-icon"></span><div><b>75%</b><span>Sed ut perspiciatis unde omnis iste natus error sit voluptatem.</span></div></div>
  <div class="stat"><span class="stat-icon"></span><div><b>90%</b><span>Sed ut perspiciatis unde omnis iste natus error sit voluptatem.</span></div></div>
</div>

<!-- recruiting -->
<section class="recruit abs" style="top:2323px;height:612px">
  <h2 style="top:70px">BETTER <span class="accent">CANDIDATES.</span><br>BETTER <span class="accent">RECRUITING.</span></h2>
  <div class="rule" style="left:153px;top:178px"></div>
  <p style="top:220px">Sed ut perspiciatis unde omnis iste natus error sit voluptatem accusantium doloremque laudantium, totam rem aperiam, eaque ipsa quae ab illo inventore veritatis et quasi architecto beatae vitae dicta sunt explicabo. Nemo enim ipsam voluptatem quia voluptas sit aspernatur aut odit aut fugit, sed quia consequuntur magni dolores eos qui ratione voluptatem sequi nesciunt. Neque porro quisquam est, qui dolorem ipsum quia dolor sit amet</p>
  <p style="top:370px">At vero eos et accusamus et iusto odio dignissimos ducimus qui blanditiis praesentium voluptatum deleniti atque corrupti quos dolores et quas molestias excepturi sint occaecati cupiditate non provident, similique sunt in culpa qui officia deserunt mollitia animi, id est laborum et dolorum fuga. Et harum quidem rerum facilis est et expedita distinctio.</p>
  <div class="btn" style="left:153px;top:504px;width:106px;height:34px">Hire Now</div>
  <div class="photo" role="img" aria-label="Team meeting seated in a bright office" style="left:645px;top:74px;width:407px;height:458px;background:linear-gradient(135deg,#f3e2b8,#b79d72 40%,#3f3b3a 100%)"></div>
</section>

<!-- testimonials -->
<section class="testimonials abs">
  <h2 class="section-title" style="top:52px">CUSTOMER <span class="accent">TESTIMONIALS</span></h2>
  <div class="rule" style="left:579px;top:125px"></div>
  <div class="arrow-btn" style="left:72px;top:274px"></div>
  <div class="arrow-btn" style="left:1091px;top:274px"></div>
  <svg class="abs" style="left:0;top:0" width="1200" height="400"><path d="M94 286 L86 292 L94 298M1105 286 L1113 292 L1105 298" fill="none" stroke="#a9b0c0" stroke-width="1.5"/></svg>

  <div class="t-card t-side" style="left:150px;top:205px;width:280px;height:200px">
    <div class="q" style="font-size:40px;margin:18px 0 4px">“</div>
    <p>Sed ut perspiciatis unde omnis iste natus error sit voluptatem accusantium doloremque laudantium, totam rem aperiam, eaque ipsa quae ab illo inventore veritatis et quasi dicta sunt explicabo nemo enim ipsam.</p>
  </div>
  <div class="t-card t-side" style="left:772px;top:205px;width:280px;height:200px">
    <div class="q" style="font-size:40px;margin:18px 0 4px">“</div>
    <p>Sed ut perspiciatis unde omnis iste natus error sit voluptatem accusantium doloremque laudantium, totam rem aperiam, eaque ipsa quae ab illo inventore veritatis et quasi dicta sunt explicabo nemo enim ipsam.</p>
  </div>
  <div class="author" style="left:272px;top:420px"><span class="avatar" role="img" aria-label="Client portrait" style="width:28px;height:28px"></span><div><b style="font-size:9px">Dana Whitlow</b><span style="font-size:8px">2 Days Ago</span></div></div>
  <div class="author" style="left:836px;top:420px"><span class="avatar" role="img" aria-label="Client portrait" style="width:28px;height:28px"></span><div><b style="font-size:9px">Dana Whitlow</b><span style="font-size:8px">2 Days Ago</span></div></div>

  <div class="t-card t-main" style="left:358px;top:170px;width:477px;height:270px">
    <div class="q" style="font-size:64px;margin:26px 0 0">“</div>
    <p>Sed ut perspiciatis unde omnis iste natus error sit voluptatem accusantium doloremque laudantium, totam rem aperiam, eaque ipsa quae ab illo inventore veritatis et quasi architecto beatae vitae dicta sunt explicabo. Nemo enim ipsam voluptatem quia voluptas sit aspernatur aut odit aut fugit, sed quia consequuntur magni dolores eos qui ratione voluptatem sequi nesciunt. Neque porro quisquam est, qui dolorem ipsum quia dolor sit amet</p>
  </div>
  <svg class="abs" style="left:586px;top:439px" width="24" height="14"><path d="M0 0 L12 13 L24 0Z" fill="#fff"/></svg>
  <div class="author" style="left:528px;top:470px"><span class="avatar" role="img" aria-label="Client portrait" style="width:44px;height:44px"></span><div><b style="font-size:13px">Dana Whitlow</b><span style="font-size:11px">2 Days Ago</span></div></div>
</section>

<!-- blog -->
<section class="blog abs">
  <h2 class="section-title" style="top:56px">LATEST <span class="accent">BLOG</span></h2>
  <div class="rule" style="left:579px;top:124px"></div>
  <article class="post featured" style="left:152px">
    <div class="img" role="img" aria-label="Smiling businessman shaking hands in an office" style="background:linear-gradient(135deg,#c9d3de,#7a8ba0)"></div>
    <h3>Lorem ipsum dolor sit amet consectetur adipiscing</h3>
    <p>Sed ut perspiciatis unde omnis iste natus error sit voluptatem accus antium doloremque laudantium, totam rem aperiam, eaque ipsa quae.</p>
    <div class="btn">Read More</div>
  </article>
  <article class="post" style="left:462px">
    <div class="img" role="img" aria-label="Businesswoman seated at a desk in a city office" style="background:linear-gradient(135deg,#e4e8ee,#9aa5b4)"></div>
    <h3>Lorem ipsum dolor sit amet consectetur adipiscing</h3>
    <p>Sed ut perspiciatis unde omnis iste natus error sit voluptatem accus antium doloremque laudantium, totam rem aperiam, eaque ipsa quae.</p>
    <div class="btn">Read More</div>
  </article>
  <article class="post" style="left:769px">
    <div class="img" role="img" aria-label="Hand selecting one figure from a crowd of figurines" style="background:linear-gradient(135deg,#3a4150,#15181f 70%,#8a1d1d 100%)"></div>
    <h3>Lorem ipsum dolor sit amet consectetur adipiscing</h3>
    <p>Sed ut perspiciatis unde omnis iste natus error sit voluptatem accus antium doloremque laudantium, totam rem aperiam, eaque ipsa quae.</p>
    <div class="btn">Read More</div>
  </article>
</section>

<!-- call to action -->
<section class="cta abs">
  <div class="pill-outline" style="left:532px;top:52px;width:136px;height:42px;border-color:#fff;color:#fff;font-size:17px;font-weight:500;border-radius:10px">Find Talent</div>
  <h2>CONNECT <span class="accent">WITH US</span></h2>
  <p>Lorem ipsum dolor sit amet, consectetur adipiscing elit, sed do eius<br>mod tempor incididunt ut labore et dolore magna aliqua</p>
  <div class="btn" style="left:471px;top:298px;width:130px;height:42px">Find Work</div>
  <div class="btn" style="left:613px;top:298px;width:128px;height:42px">Find Talent</div>
</section>

<!-- footer -->
<footer class="site-footer abs">
  <div class="foot-brand abs"><span class="brand-mark"></span><span class="name">Tarvenly<br>Work</span></div>
  <div class="foot-col abs" style="left:422px;top:55px;width:260px">
    <h4>Contact Us</h4><div class="bar"></div>
    <div class="contact-row"><svg width="12" height="16" viewBox="0 0 12 16"><path d="M6 0a6 6 0 016 6c0 4.5-6 10-6 10S0 10.5 0 6a6 6 0 016-6z" fill="#fff"/><circle cx="6" cy="6" r="2.2" fill="#0d2a78"/></svg><span>Harbourline Tower, 1180 Corvin Street<br>suite 900, V0X 1A0 Eastmere, BC</span></div>
    <div class="contact-row"><svg width="12" height="14" viewBox="0 0 24 24"><path d="M6.6 10.8a15.1 15.1 0 006.6 6.6l2.2-2.2a1 1 0 011-.25 11.4 11.4 0 003.6.57 1 1 0 011 1V20a1 1 0 01-1 1A17 17 0 013 4a1 1 0 011-1h3.5a1 1 0 011 1c0 1.25.2 2.45.57 3.57a1 1 0 01-.25 1z" fill="#fff"/></svg><span>778-555-0193</span></div>
    <div class="contact-row"><svg width="13" height="12" viewBox="0 0 13 12"><rect width="13" height="10" y="1" rx="1.5" fill="#fff"/><path d="M1 2l5.5 4L12 2" fill="none" stroke="#0d2a78" stroke-width="1.2"/></svg><span>hello@tarvenlywork.ca</span></div>
  </div>
  <div class="foot-col abs" style="left:713px;top:55px">
    <h4>Menu</h4><div class="bar"></div>
    <ul><li>Home</li><li>Candidates</li><li>Employers</li><li>Services</li><li>About Us</li><li>Contact Us</li></ul>
  </div>
  <div class="foot-col abs" style="left:863px;top:55px">
    <h4>Follow Us</h4><div class="bar"></div>
    <div class="socials"><i></i><i></i><i></i><i></i><i></i></div>
  </div>
  <div class="btn" style="left:863px;top:178px;width:186px;height:42px;font-size:14px;font-weight:700">Register</div>
  <div class="copyright abs">Copyright © 2026 All Rights Reserved</div>
</footer>

</body>
</html>
```